New Business Card Design Project

I need a design for business cards, i am an electrical business called "Corvane Electrical and Communications" i need the cards to be double sided with the company logo on the back (attached) the front needs to say my company name, web site, email address, telephone number, and ABN number and electrical license number. I am open to different arrangements of the information but would like the background to be incorporating something electrical or something that looks smart. open to all additional ideas also.

The company colours are orange and grey see logo attached.

Business Name: Corvane Electrical and Communications
Website: corvaneelectricalandcomms.example.com.au
Email: brent@corvaneelectricalandcomms.example.com.au
Telephone(mobile): 0481209736
ABN: 71208349162
Lic No: 418273D

Target Market(s)

Business entities, Project Managers, Accounts, Clients

Industry/Entity Type

Electrician

Contact Information for Business Card

I need a design for business cards, i am an electrical business called "Corvane Electrical and Communications" i need the cards to be double sided with the company logo on the back (attached) the front needs to say my company name

Font styles to use
Serif
Sans Serif

Colors
f37122
5c5c5c

Requirements
Must have
• Must have the Logo on the back open to different ways of it being on the back but had in mind to keep it central but again open to other options
Nice to have
• A real modern cool background that is eye catching yet contemporary
Should not have
• No backgrounds of a light bulb or plug or anything like that

```html
<!DOCTYPE html>
<html lang="en">
<head>
<meta charset="utf-8">
<title>Corvane Electrical and Communications – Business Cards</title>
<link href="https://fonts.googleapis.com/css2?family=Open+Sans:wght@400;600&display=swap" rel="stylesheet">
<style>
  :root {
    --backdrop: #3a3a3a;
    --card: #050505;
    --amber: #f6a821;
    --white: #ffffff;
    --shadow: rgba(0, 0, 0, 0.55);
  }
  * { margin: 0; padding: 0; box-sizing: border-box; }
  html, body {
    width: 1200px;
    height: 900px;
    overflow: hidden;
    background: var(--backdrop);
    font-family: "Open Sans", sans-serif;
  }
  .canvas {
    position: relative;
    width: 1200px;
    height: 900px;
  }
  .card {
    position: absolute;
    width: 600px;
    height: 367px;
    background: var(--card);
    border-radius: 22px;
    box-shadow: 0 18px 40px var(--shadow);
    overflow: hidden;
  }
  .card--back { left: 90px; top: 60px; }
  .card--front { left: 510px; top: 470px; }

  /* back side */
  .brand-name {
    color: var(--amber);
    font-weight: 600;
    text-transform: uppercase;
    letter-spacing: 0.04em;
    line-height: 1.15;
  }
  .card--back .brand {
    position: absolute;
    left: 0; right: 0; top: 112px;
    display: flex;
    align-items: center;
    justify-content: center;
    gap: 16px;
  }
  .brand-dot {
    width: 22px; height: 22px;
    border-radius: 50%;
    background: var(--amber);
    flex: none;
  }
  .card--back .brand-name { font-size: 30px; text-align: left; }
  .website-line {
    position: absolute;
    left: 0; right: 0; bottom: 58px;
    text-align: center;
    font-size: 15px;
    color: var(--white);
    font-weight: 600;
  }
  .website-line .accent { color: var(--amber); }

  /* front side */
  .card--front .brand {
    position: absolute;
    left: 40px; top: 140px;
    width: 230px;
    display: flex;
    align-items: center;
    gap: 10px;
  }
  .card--front .brand-dot { width: 14px; height: 14px; }
  .card--front .brand-name { font-size: 17px; }
  .divider {
    position: absolute;
    left: 292px; top: 82px;
    width: 1px; height: 180px;
    background: var(--amber);
  }
  .contact {
    position: absolute;
    left: 306px; top: 82px;
    width: 280px;
  }
  .contact__name {
    color: var(--amber);
    font-size: 21px;
    font-weight: 400;
    text-transform: uppercase;
    letter-spacing: 0.01em;
  }
  .contact__role {
    color: var(--white);
    font-size: 11px;
    text-transform: uppercase;
    margin-bottom: 8px;
  }
  .contact__list { list-style: none; }
  .contact__item {
    display: flex;
    align-items: center;
    gap: 8px;
    color: var(--white);
    font-size: 10.5px;
    line-height: 19px;
    white-space: nowrap;
  }
  .contact__item svg { width: 11px; height: 11px; flex: none; }
  .contact__item .label { color: var(--amber); }
  .contact__item--plain { padding-left: 19px; }
</style>
</head>
<body>
<main class="canvas">

  <section class="card card--back" aria-label="Card back">
    <div class="brand">
      <span class="brand-dot"></span>
      <span class="brand-name">Corvane Electrical<br>and Communications</span>
    </div>
    <p class="website-line">www.<span class="accent">corvaneelectricalandcomms</span>.example.com.au</p>
  </section>

  <section class="card card--front" aria-label="Card front">
    <div class="brand">
      <span class="brand-dot"></span>
      <span class="brand-name">Corvane Electrical and Communications</span>
    </div>
    <div class="divider"></div>
    <div class="contact">
      <h1 class="contact__name">Marlo Quinlan</h1>
      <p class="contact__role">Director</p>
      <ul class="contact__list">
        <li class="contact__item">
          <svg viewBox="0 0 24 24" aria-hidden="true"><path fill="#f6a821" d="M6.6 10.8a15 15 0 0 0 6.6 6.6l2.2-2.2a1 1 0 0 1 1-.25 11.4 11.4 0 0 0 3.6.57 1 1 0 0 1 1 1V20a1 1 0 0 1-1 1A17 17 0 0 1 3 4a1 1 0 0 1 1-1h3.5a1 1 0 0 1 1 1c0 1.25.2 2.45.57 3.57a1 1 0 0 1-.25 1z"/></svg>
          0481-209-736
        </li>
        <li class="contact__item">
          <svg viewBox="0 0 24 24" aria-hidden="true"><rect x="2" y="5" width="20" height="14" rx="2" fill="none" stroke="#f6a821" stroke-width="2"/><path d="M2 6l10 7 10-7" fill="none" stroke="#f6a821" stroke-width="2"/></svg>
          brent@corvaneelectricalandcomms.example.com.au
        </li>
        <li class="contact__item">
          <svg viewBox="0 0 24 24" aria-hidden="true"><circle cx="12" cy="12" r="10" fill="none" stroke="#f6a821" stroke-width="2"/><path d="M2 12h20M12 2c3 3 3 17 0 20M12 2c-3 3-3 17 0 20" fill="none" stroke="#f6a821" stroke-width="1.6"/></svg>
          www.corvaneelectricalandcomms.example.com.au
        </li>
        <li class="contact__item contact__item--plain"><span class="label">ABN:</span> 71208349162</li>
        <li class="contact__item contact__item--plain"><span class="label">Lic No:</span> 418273D</li>
      </ul>
    </div>
  </section>

</main>
</body>
</html>
```